Professional Chatterly Banner, Business Cards, Door Hang Tags, Service Flyer for Pest Control Company

There are really 4 things I need designed but Pixel Bazaar doesn't have them to package together. I am needing to get a Professional Chatterly Banner, Business Cards, Door Hang Tags, and Service Flyer for a Pest Control Company. I already have a logo that I will attach to the project along with content a for each one of these tasks. Please see document attached labeled All Design Content & Flyer Content.
Industry/Entity Type
Pest Control
Look and feel
Each slider illustrates characteristics of the customer's brand and the style your logo design should communicate.

```html
<!DOCTYPE html>
<html lang="en">
<head>
<meta charset="utf-8">
<title>Tangerine Grove Pest Control – Door Hangers</title>
<link rel="stylesheet" href="https://fonts.googleapis.com/css2?family=Barlow+Condensed:ital,wght@0,700;1,600;1,700&family=Inter:wght@400;500&display=swap">
<style>
  :root {
    --ink: #0b0b0b;
    --paper: #f4f4f4;
    --orange: #f26b21;
    --icon-fill: #3a3a3a;
    --white: #ffffff;
    --stage: #e0e0e0;
  }
  * { box-sizing: border-box; margin: 0; padding: 0; }
  html, body { width: 1124px; height: 1200px; overflow: hidden; }
  body { background: var(--stage); font-family: "Inter", Arial, sans-serif; }

  .canvas { position: relative; width: 1124px; height: 1200px; }

  .hanger { position: absolute; top: 130px; width: 340px; height: 940px; }
  .hanger--about { left: 150px; }
  .hanger--services { left: 636px; }

  .hanger__shape { position: absolute; inset: 0; }

  .band { position: absolute; left: 0; width: 340px; }
  .band--header { top: 300px; height: 98px; text-align: center; padding-top: 20px; }
  .band--body { top: 398px; height: 312px; background: var(--paper); text-align: center; }
  .band--cta { top: 710px; height: 142px; background: var(--orange); text-align: center; color: var(--white); }
  .band--offer { top: 852px; height: 88px; text-align: center; }

  .brand { font-family: "Barlow Condensed", "Arial Narrow", sans-serif; font-weight: 700; color: var(--orange); line-height: 1; }
  .brand__name { font-size: 34px; letter-spacing: 1px; display: block; }
  .brand__tag { font-size: 13px; letter-spacing: 9px; display: block; margin-top: 6px; padding-left: 9px; }

  .condensed { font-family: "Barlow Condensed", "Arial Narrow", sans-serif; font-style: italic; font-weight: 700; text-transform: uppercase; line-height: 1; }

  .intro { color: var(--ink); font-size: 15px; line-height: 20px; letter-spacing: -0.5px; padding: 14px 10px 0; white-space: nowrap; }

  .motto {
    display: inline-block; margin-top: 16px; width: 212px; padding: 8px 6px;
    background: var(--ink); color: var(--white); font-size: 19px; line-height: 20px;
    box-shadow: 3px 3px 0 var(--orange); transform: rotate(-0.6deg);
  }

  .promise { color: var(--orange); font-size: 13px; line-height: 17.5px; letter-spacing: -0.35px; padding: 12px 10px 0; white-space: nowrap; }

  .cta__call { font-size: 31px; padding-top: 16px; }
  .cta__quote { font-size: 22px; margin-top: 2px; }
  .cta__phone { font-size: 34px; font-weight: 600; margin-top: 6px; }
  .cta__web { display: flex; align-items: center; justify-content: center; gap: 12px; margin-top: 6px; font-size: 13px; letter-spacing: -0.2px; }

  .offer { display: inline-flex; align-items: center; gap: 6px; margin-top: 16px; }
  .offer__amount { color: var(--orange); font-size: 42px; }
  .offer__detail { color: var(--white); font-size: 18px; text-align: left; line-height: 0.95; }
  .offer__note { color: var(--white); font-size: 9.5px; letter-spacing: -0.2px; margin-top: -2px; }

  .services-title {
    display: inline-block; margin-top: 15px; width: 160px; padding: 8px 0 6px;
    background: var(--orange); color: var(--white); font-size: 30px;
    box-shadow: 2px 3px 0 var(--ink);
  }

  .service-grid {
    list-style: none; display: grid; grid-template-columns: 120px 110px;
    column-gap: 4px; row-gap: 18px; margin: 28px 0 0 66px; text-align: left;
  }
  .service { display: flex; align-items: center; gap: 8px; color: var(--ink); font-size: 18px; line-height: 0.95; min-height: 24px; }
  .service__icon {
    flex: none; width: 20px; height: 20px; border-radius: 3px;
    background: var(--icon-fill);
  }
</style>
</head>
<body>
<main class="canvas">

  <!-- Door hanger: about the company -->
  <article class="hanger hanger--about">
    <svg class="hanger__shape" viewBox="0 0 340 940" width="340" height="940" aria-hidden="true">
      <path fill="#0b0b0b" d="M340,320 V140 C340,60 270,0 170,0 C70,0 5,60 5,140 V185 C5,210 25,225 45,225 C70,225 90,210 90,185 V130 C90,105 105,90 130,90 H214 C237,90 252,105 252,130 V300 H30 C12,300 2,312 2,330 V905 C2,925 17,940 37,940 H305 C325,940 340,925 340,905 Z"/>
    </svg>

    <header class="band band--header">
      <p class="brand"><span class="brand__name">TANGERINE GROVE</span><span class="brand__tag">PEST CONTROL</span></p>
    </header>

    <section class="band band--body">
      <p class="intro">We are a locally owned and operated,<br>with 10 years of industry experience our<br>family is committed to delivering<br>exceptional customer service and<br>high-quality results.</p>
      <p class="motto condensed">We strive for excellence in all that we do.</p>
      <p class="promise">We treat each and every customer like a<br>member of our family. When you partner with<br>us, you can enjoy hassle-free services,<br>expert care, and peace of mind knowing you<br>and your home are protected from pests for<br>years to come.</p>
    </section>

    <section class="band band--cta">
      <p class="cta__call condensed">Call now!</p>
      <p class="cta__quote condensed">For a free quote</p>
      <p class="cta__phone condensed">(555) 214-7780</p>
      <p class="cta__web">
        <svg width="12" height="12" viewBox="0 0 12 12" aria-hidden="true"><circle cx="6" cy="6" r="5.5" fill="#fff"/><path d="M0.5,6 H11.5 M6,0.5 C3,3 3,9 6,11.5 M6,0.5 C9,3 9,9 6,11.5" stroke="#f26b21" stroke-width="0.9" fill="none"/></svg>
        www.tangerinegrovepest.com
      </p>
    </section>

    <footer class="band band--offer">
      <div class="offer">
        <span class="offer__amount condensed">$50 off</span>
        <span class="offer__detail condensed">One time<br>service</span>
      </div>
      <p class="offer__note">New Customers Only</p>
    </footer>
  </article>

  <!-- Door hanger: services -->
  <article class="hanger hanger--services">
    <svg class="hanger__shape" viewBox="0 0 340 940" width="340" height="940" aria-hidden="true">
      <path fill="#0b0b0b" d="M340,320 V140 C340,60 270,0 170,0 C70,0 5,60 5,140 V185 C5,210 25,225 45,225 C70,225 90,210 90,185 V130 C90,105 105,90 130,90 H214 C237,90 252,105 252,130 V300 H30 C12,300 2,312 2,330 V905 C2,925 17,940 37,940 H305 C325,940 340,925 340,905 Z"/>
    </svg>

    <header class="band band--header">
      <p class="brand"><span class="brand__name">TANGERINE GROVE</span><span class="brand__tag">PEST CONTROL</span></p>
    </header>

    <section class="band band--body">
      <h2 class="services-title condensed">Our services</h2>
      <ul class="service-grid">
        <li class="service condensed"><span class="service__icon" role="img" aria-label="Ant silhouette"></span>Ants</li>
        <li class="service condensed"><span class="service__icon" role="img" aria-label="Rat silhouette"></span>Rats</li>
        <li class="service condensed"><span class="service__icon" role="img" aria-label="Mosquito silhouette"></span>Mosquitos</li>
        <li class="service condensed"><span class="service__icon" role="img" aria-label="Mouse silhouette"></span>Mice</li>
        <li class="service condensed"><span class="service__icon" role="img" aria-label="Flea silhouette"></span>Fleas</li>
        <li class="service condensed"><span class="service__icon" role="img" aria-label="Termite silhouette"></span>Termites</li>
        <li class="service condensed"><span class="service__icon" role="img" aria-label="Cockroach silhouette"></span>Roaches</li>
        <li class="service condensed"><span class="service__icon" role="img" aria-label="Spider silhouette"></span>Spiders</li>
        <li class="service condensed"><span class="service__icon" role="img" aria-label="Wasp silhouette"></span>Stinging<br>insects</li>
        <li class="service condensed"><span class="service__icon" role="img" aria-label="Other pests"></span>&amp; More</li>
      </ul>
    </section>

    <section class="band band--cta">
      <p class="cta__call condensed">Call now!</p>
      <p class="cta__quote condensed">For a free quote</p>
      <p class="cta__phone condensed">(555) 214-7780</p>
      <p class="cta__web">
        <svg width="12" height="12" viewBox="0 0 12 12" aria-hidden="true"><circle cx="6" cy="6" r="5.5" fill="#fff"/><path d="M0.5,6 H11.5 M6,0.5 C3,3 3,9 6,11.5 M6,0.5 C9,3 9,9 6,11.5" stroke="#f26b21" stroke-width="0.9" fill="none"/></svg>
        www.tangerinegrovepest.com
      </p>
    </section>

    <footer class="band band--offer">
      <div class="offer">
        <span class="offer__amount condensed">$25 off</span>
        <span class="offer__detail condensed">One time<br>service</span>
      </div>
      <p class="offer__note">New Customers Only</p>
    </footer>
  </article>

</main>
</body>
</html>
```